Web design for business website

I need a web design for a business website for one of our clients who is specialized in alarm management software. I would like you to design 3 web pages, one for each of the 3 pages. You need to process the corporate identity of our client to the web design. This means the colors of the logo (red and black) should definitely show up on all of the 3 pages. Find the logo file for the logo of our customer. To increase readability I suggest you use a white/light background. All suggestions are welcome.

Please kindly download atttached Webdesign.zip and read the project brief first. The project brief refers to all other files of the zip file. Your design must have exactly the same structure as the wireframes.
Updates

Target Market(s)

B2B, Alarm management

Industry/Entity Type

Business

Number of Pages Required

3 page

Requirements
Must have
• The web design must have exactly the same structure as the wireframes and needs to contain the colors of the company logo.

```html
<!DOCTYPE html>
<html lang="en">
<head>
<meta charset="utf-8">
<title>Veralyn – Real-time reasoning solutions</title>
<link href="https://fonts.googleapis.com/css2?family=Montserrat:wght@400;700;800&family=Open+Sans:wght@400;600;700&display=swap" rel="stylesheet">
<style>
:root{
  --orange:#e8461a;
  --orange-dark:#d63c12;
  --navy:#1c1a33;
  --black:#111;
  --topbar:#151515;
  --header:#ececec;
  --footer:#1b1b1b;
  --footer-text:#5e5e5e;
  --footer-head:#3c3c3c;
  --text:#333;
  --white:#fff;
}
*{box-sizing:border-box;margin:0;padding:0}
html,body{width:740px;height:1200px;overflow:hidden}
body{font-family:"Open Sans",sans-serif;color:var(--text);background:var(--white);position:relative}
.abs{position:absolute}
.topbar{top:0;left:0;width:740px;height:21px;background:var(--topbar);color:#aaa;font-size:8px}
.topbar .phone{left:60px;top:5px;display:flex;gap:5px;align-items:center}
.topbar .lang{left:600px;top:0;height:21px;width:57px;border-left:1px solid #333;border-right:1px solid #333;display:flex;align-items:center;justify-content:center;gap:8px}
.topbar .search{left:657px;top:0;height:21px;width:22px;border-right:1px solid #333;display:flex;align-items:center;justify-content:center}
.header{top:21px;left:0;width:740px;height:53px;background:var(--header)}
.logo{left:60px;top:12px;display:flex;align-items:center;gap:6px}
.logo .dot{width:26px;height:26px;border-radius:50%;background:var(--orange)}
.logo .name{font-family:"Montserrat",sans-serif;font-weight:800;font-size:20px;color:var(--black);letter-spacing:1.5px;line-height:1}
.logo .tag{font-size:6px;color:#444;margin-top:1px}
.acts{right:60px;top:10px;display:flex;gap:11px}
.act{width:32px;height:32px;border-radius:50%;background:var(--orange);color:#fff;font-size:5px;display:flex;flex-direction:column;align-items:center;justify-content:center;gap:2px}
.nav{top:74px;left:0;width:740px;height:26px;background:var(--navy)}
.nav ul{list-style:none;display:flex;position:absolute;left:61px;top:3px}
.nav li{height:20px;font-size:7.5px;color:#fff;display:flex;align-items:center;justify-content:center}
.nav li.home{background:var(--orange);width:52px;font-weight:700}
.hero{top:100px;left:0;width:740px;height:265px;background:linear-gradient(180deg,#c9d3d8 0%,#e7e3d6 45%,#cfd6d6 100%)}
.hero-txt{top:84px;left:0;width:740px;text-align:center}
.hero h3{font-size:10px;font-weight:700;color:#222}
.hero h2{font-family:"Open Sans",sans-serif;font-weight:400;font-size:16px;color:#222;margin-top:4px}
.hero h2 span,.welcome h2 span{color:var(--orange)}
.hero p{font-size:6px;color:#444;width:310px;margin:7px auto 0;line-height:1.5}
.btn{background:var(--orange);color:#fff;font-size:7px;font-weight:600;display:flex;align-items:center;justify-content:center}
.hero .btn{width:84px;height:27px;margin:13px auto 0}
.arrow{width:31px;height:31px;top:117px;display:flex;align-items:center;justify-content:center}
.arrow.prev{left:30px;background:rgba(255,255,255,.45)}
.arrow.next{left:679px;background:var(--orange)}
.welcome{top:410px;left:0;width:740px;text-align:center}
.welcome h1{font-family:"Montserrat",sans-serif;font-weight:800;font-size:30px;color:var(--navy);line-height:1}
.welcome h2{font-weight:400;font-size:21px;color:#222;margin-top:8px}
.about{top:512px;left:61px;width:618px;height:212px;display:flex}
.about .photo{width:282px;height:212px;background:linear-gradient(135deg,#c9d0d2,#7fb8c4 55%,#9aa2a6)}
.about .panel{flex:1;background:linear-gradient(135deg,#e0481a,#ef6a3a 60%,#e4521f);color:#fff;padding:22px 14px 0 13px}
.about h4{font-family:"Montserrat",sans-serif;font-weight:700;font-size:15px;margin-bottom:15px}
.about p{font-size:7.2px;line-height:1.46;margin-bottom:10px}
.divider{top:778px;left:0;width:740px;height:1px;background:#e4e4e4}
.clients{top:806px;left:50px;width:640px;height:22px;display:flex;align-items:center;justify-content:space-between}
.client{font-family:"Open Sans",sans-serif;font-weight:700;font-size:11px;color:#1c3f7a;display:flex;align-items:center;gap:4px}
.client i{display:block;width:10px;height:10px;border-radius:50%;background:#2a8a3c}
.band{top:857px;left:0;width:740px;height:132px;background:linear-gradient(180deg,#d9dcd9,#ecebe2 50%,#dfe2de)}
.band h5{font-family:"Montserrat",sans-serif;font-weight:400;font-size:18px;color:#222;letter-spacing:.5px}
.band h5 span{color:var(--orange)}
.follow{left:61px;top:34px}
.socials{display:flex;gap:6px;margin-top:12px}
.socials div{width:26px;height:26px;background:#8d8d8d}
.socials div.first{background:#2d4f9c}
.subscribe{left:272px;top:34px}
.form{display:flex;margin-top:12px}
.form .input{width:333px;height:26px;border:1.5px solid var(--navy);background:rgba(255,255,255,.6);font-size:7px;color:#888;padding:8px 14px}
.form .btn{width:74px;height:26px;background:var(--navy);font-weight:700}
.footer{top:989px;left:0;width:740px;height:179px;background:var(--footer)}
.col{top:46px;font-size:7.4px;color:var(--footer-text);line-height:11.6px}
.col h6{font-family:"Montserrat",sans-serif;font-weight:400;font-size:9.5px;color:var(--footer-head);margin-bottom:8px}
.col .hl{color:var(--orange)}
.col .row{display:flex;gap:9px;align-items:center;margin-bottom:6px}
.bottom{top:1168px;left:0;width:740px;height:32px;background:var(--footer);border-top:1px solid #2a2a2a;font-size:6px;color:#444;text-align:center;padding-top:12px}
.bottom span{color:var(--orange)}
</style>
</head>
<body>
<div class="abs topbar">
  <div class="abs phone"><svg width="7" height="7" viewBox="0 0 10 10"><path d="M2 1l2 2-1 1.5c.8 1.5 1.7 2.4 3 3L7.5 6l2 2-1.5 1.5C4 9 1 6 .5 2.5z" fill="#888"/></svg>+31 (0)40 5518 306</div>
  <div class="abs lang"><svg width="6" height="4" viewBox="0 0 6 4"><path d="M0 0h6L3 4z" fill="#888"/></svg>ENG</div>
  <div class="abs search"><svg width="8" height="8" viewBox="0 0 10 10"><circle cx="4" cy="4" r="3" stroke="#bbb" stroke-width="1.4" fill="none"/><path d="M6.3 6.3L9 9" stroke="#bbb" stroke-width="1.5"/></svg></div>
</div>

<header class="abs header">
  <div class="abs logo">
    <div class="dot"></div>
    <div><div class="name">VERALYN</div><div class="tag">Real-time reasoning solutions</div></div>
  </div>
  <div class="abs acts">
    <div class="act"><svg width="8" height="8" viewBox="0 0 10 10"><circle cx="5" cy="3" r="2.3" fill="#fff"/><path d="M1 10c0-3 1.8-4.5 4-4.5S9 7 9 10z" fill="#fff"/></svg>ACCOUNT</div>
    <div class="act"><svg width="8" height="8" viewBox="0 0 10 10"><path d="M1 4h4V2l4 3-4 3V6H1z" fill="#fff"/></svg>SIGN UP</div>
    <div class="act"><svg width="8" height="8" viewBox="0 0 10 10"><rect x="1" y="4.5" width="7" height="5" fill="#fff"/><path d="M3 4.5V3a2.5 2.5 0 015 0" stroke="#fff" stroke-width="1.3" fill="none"/></svg>LOG IN</div>
  </div>
</header>

<nav class="abs nav">
  <ul>
    <li class="home">HOME</li>
    <li style="width:80px">INDUSTRY</li>
    <li style="width:74px">TELECOM</li>
    <li style="width:68px">POWER</li>
    <li style="width:70px">UTILITIES</li>
    <li style="width:64px">INFRA</li>
    <li style="width:86px;justify-content:flex-start;padding-left:12px">STORE</li>
  </ul>
</nav>

<section class="abs hero" role="img" aria-label="Refinery plant lit up at dusk">
  <div class="abs hero-txt">
    <h3>HELLO WE ARE</h3>
    <h2><span>VERALYN</span> Real-time reasoning solutions</h2>
    <p>Companies have invested to get data out of processes. New technologies have been developed to get real-time data out of the harshest places, like oil-well drill heads or the Great Barrier Riff.</p>
    <div class="btn">READ MORE</div>
  </div>
  <div class="abs arrow prev"><svg width="6" height="8" viewBox="0 0 6 8"><path d="M5 1L2 4l3 3" stroke="var(--orange)" stroke-width="1.6" fill="none"/></svg></div>
  <div class="abs arrow next"><svg width="6" height="8" viewBox="0 0 6 8"><path d="M1 1l3 3-3 3" stroke="#fff" stroke-width="1.6" fill="none"/></svg></div>
</section>

<section class="abs welcome">
  <h1>WELCOME TO</h1>
  <h2><span>VERALYN</span> Real-time reasoning solutions</h2>
</section>

<section class="abs about">
  <div class="photo" role="img" aria-label="Pressure transmitter with blue and yellow cables"></div>
  <div class="panel">
    <h4>About Us</h4>
    <p>Companies have invested to get data out of processes. New technologies have been developed to get real-time data out of the harshest places, like oil-well drill heads or the Great Barrier Riff. Data in itself means nothing without the context the data is collected in. Example: data from equipment under maintenance does not provide information to operations. Information - data which is valid and meaningful can overwhelm any user without the proper knowledge to interpret this information.</p>
    <p>Veralyn technology enables easy application of such knowledge in a comprehensible – visual – representation and makes hypothetical reasoning with information possible providing meaningful advisories to subscribers when they need it or when it is required that they are made aware of a situation which requires their attention.</p>
  </div>
</section>

<div class="abs divider"></div>

<section class="abs clients">
  <svg width="8" height="12" viewBox="0 0 8 12"><path d="M7 1L2 6l5 5" stroke="var(--orange)" stroke-width="1.6" fill="none"/></svg>
  <div class="client">Norvale</div>
  <div class="client">Ketterby</div>
  <div class="client"><i></i>Orlan</div>
  <div class="client">Mivex</div>
  <div class="client" style="color:#1d6b2f">Brauwald</div>
  <div class="client" style="color:#d8321e">Cordane</div>
  <div class="client">Tideholm</div>
  <svg width="8" height="12" viewBox="0 0 8 12"><path d="M1 1l5 5-5 5" stroke="#222" stroke-width="1.6" fill="none"/></svg>
</section>

<section class="abs band" role="img" aria-label="Faded refinery plant backdrop">
  <div class="abs follow">
    <h5>FOLLOW <span>US ON :</span></h5>
    <div class="socials"><div class="first"></div><div></div><div></div><div></div><div></div></div>
  </div>
  <div class="abs subscribe">
    <h5>SUBSCRIBE <span>NOW :</span></h5>
    <div class="form"><div class="input">Enter Your Email Adress</div><div class="btn">SUBSCRIBE</div></div>
  </div>
</section>

<footer class="abs footer">
  <div class="abs col" style="left:61px"><h6>SOLUTIONS</h6><div class="hl">KITE Alarm Reporting</div><div>KITE Alarm Analysis</div><div>KITE Alarm Expert</div><div>USE</div></div>
  <div class="abs col" style="left:166px"><h6>INDUSTRIES</h6><div>Industry</div><div>Telecom</div><div>Power</div><div>Utilites</div><div>Infra</div></div>
  <div class="abs col" style="left:273px"><h6>ABOUT US</h6><div>Company</div><div>Overview</div><div>Leadership</div><div>Partners</div><div>Locations</div></div>
  <div class="abs col" style="left:378px"><h6>NEWS</h6><div>Product News</div><div>Partner News</div><div>Events</div><div>Press Releases</div><div>Vacancies</div></div>
  <div class="abs col" style="left:537px"><h6>CONTACT US</h6>
    <div class="row"><svg width="7" height="7" viewBox="0 0 10 10"><path d="M2 1l2 2-1 1.5c.8 1.5 1.7 2.4 3 3L7.5 6l2 2-1.5 1.5C4 9 1 6 .5 2.5z" fill="#555"/></svg>+31 (0)40 5518 306</div>
    <div class="row"><svg width="7" height="6" viewBox="0 0 10 8"><rect width="10" height="8" fill="#555"/><path d="M0 0l5 4 5-4" stroke="#1b1b1b" fill="none"/></svg>hello@veralyn.example</div>
    <div class="row"><svg width="6" height="8" viewBox="0 0 8 11"><path d="M4 0a4 4 0 014 4c0 3-4 7-4 7S0 7 0 4a4 4 0 014-4z" fill="#555"/><circle cx="4" cy="4" r="1.5" fill="#1b1b1b"/></svg>Kanaalweg 12, Veralyn Leiden</div>
  </div>
</footer>
<div class="abs bottom">Copyright © 2105 <span>VERALYN.</span> All Rights Reserved.</div>
</body>
</html>
```